Alberta, Canada based Environmental Oilfield Consultant need a Business Card Design

We need a business card design for a year old company based in Edmonton, Alberta, Canada called Cindermoor Consulting Inc. We are environmental consultants primarily for oilfield based companies (pipeline cleanup, site consultations, environmental site training, and site evaluations).

We like the color blue or green, something very clean and crisp looking.
We don't really care if there is an otter on it but most of our work is land based and nothing really to do with oceans or larger bodies of water.

The name Cindermoor was the name of our fathers boat, and named our company that in his memory.

```html
<!DOCTYPE html>
<html lang="en">
<head>
<meta charset="utf-8">
<title>Cindermoor Consulting Inc. – Business Card</title>
<link href="https://fonts.googleapis.com/css2?family=Exo+2:wght@400;500;700&display=swap" rel="stylesheet">
<style>
  :root {
    --page-bg: #eef1f4;
    --card-bg: #ffffff;
    --band-deep: #1d56c9;
    --band-light: #4a9cf2;
    --accent-teal: #45b3c9;
    --accent-teal-soft: #a9e0ea;
    --logo-teal: #3598b8;
    --text-dark: #3b4046;
    --text-muted: #5d646c;
    --icon-blue: #2a62cf;
    --card-shadow: 0 10px 28px rgba(30, 45, 70, 0.18);
  }
  * { margin: 0; padding: 0; box-sizing: border-box; }
  html, body {
    width: 1200px; height: 900px; overflow: hidden;
    background: var(--page-bg);
    font-family: "Exo 2", sans-serif;
  }
  .canvas {
    position: relative; width: 1200px; height: 900px;
    display: flex; flex-direction: column; align-items: center; justify-content: center; gap: 60px;
  }
  .card {
    position: relative; width: 680px; height: 380px;
    background: var(--card-bg); border-radius: 34px;
    box-shadow: var(--card-shadow); overflow: hidden;
  }
  .card-band { position: absolute; inset: 0; width: 100%; height: 100%; }
  .holder {
    position: absolute; right: 44px; top: 40px; text-align: right; color: #fff;
  }
  .holder-name { font-size: 21px; font-weight: 500; letter-spacing: 1.5px; line-height: 1.2; }
  .holder-title { font-size: 15px; font-weight: 400; margin-top: 2px; line-height: 1.2; }
  .contact-list {
    position: absolute; left: 40px; top: 158px; list-style: none;
    font-size: 13px; color: var(--text-muted);
  }
  .contact-list li { display: flex; align-items: center; gap: 10px; height: 22px; }
  .contact-icon { width: 13px; height: 13px; fill: var(--icon-blue); flex: none; }
  .wordmark {
    position: absolute; right: 44px; top: 204px; text-align: right;
    color: var(--logo-teal); font-weight: 700; font-size: 44px; line-height: 1.0;
  }
  .address {
    position: absolute; right: 44px; bottom: 30px; text-align: right;
    font-size: 15px; font-style: normal; color: var(--text-dark); line-height: 1.4;
  }
  .card-back { display: flex; align-items: center; justify-content: center; }
  .wordmark-back {
    color: var(--logo-teal); font-weight: 700; font-size: 42px;
  }
</style>
</head>
<body>
<main class="canvas">
  <section class="card card-front">
    <svg class="card-band" viewBox="0 0 680 380" preserveAspectRatio="none" aria-hidden="true">
      <defs>
        <linearGradient id="bandFill" x1="0" y1="0" x2="1" y2="0.4">
          <stop offset="0" stop-color="#1d56c9"/>
          <stop offset="1" stop-color="#4a9cf2"/>
        </linearGradient>
        <linearGradient id="swooshFill" x1="0" y1="0" x2="1" y2="0">
          <stop offset="0" stop-color="#a9e0ea"/>
          <stop offset="1" stop-color="#45b3c9"/>
        </linearGradient>
      </defs>
      <path d="M0,0 H680 V200 C560,110 320,70 0,74 Z" fill="url(#bandFill)"/>
      <path d="M0,84 C320,80 560,120 680,214 L680,226 C560,132 320,92 0,96 Z" fill="url(#swooshFill)"/>
    </svg>

    <div class="holder">
      <p class="holder-name">DANIEL HARTWELL</p>
      <p class="holder-title">Managing Director</p>
    </div>

    <ul class="contact-list">
      <li><svg class="contact-icon" viewBox="0 0 16 16"><path d="M4 1l3 3-2 2c1 2 3 4 5 5l2-2 3 3-2 3C7 15 1 9 1 3z"/></svg>780 555 0142</li>
      <li><svg class="contact-icon" viewBox="0 0 16 16"><rect x="4" y="1" width="8" height="14" rx="1.5"/></svg>780 555 0142</li>
      <li><svg class="contact-icon" viewBox="0 0 16 16"><rect x="1" y="5" width="14" height="8" rx="1"/><rect x="4" y="1" width="8" height="4"/></svg>780 555 0142</li>
      <li><svg class="contact-icon" viewBox="0 0 16 16"><path d="M1 3h14v10H1z M1 3l7 6 7-6" stroke="#fff" stroke-width="1"/></svg>daniel@cindermoor.ca</li>
      <li><svg class="contact-icon" viewBox="0 0 16 16"><circle cx="8" cy="8" r="7"/></svg>www.cindermoor.ca</li>
    </ul>

    <div class="wordmark">Cindermoor<br>Consulting</div>

    <address class="address">214 Ridgeway Plaza<br>Edmonton AB</address>
  </section>

  <section class="card card-back">
    <div class="wordmark-back">Cindermoor Consulting</div>
  </section>
</main>
</body>
</html>
```